Sun Veil Custom Spray Tanning Studio

I have attached most of the information that I would like in my brochure. However, I would like the brochure to be more elegant and professional. I am no longer offering mobile tanning, however, I will be located at: 418 W Harlow Lane, Myrtle Beach, SC 29577. 843-555-0172 and I am by appointment only.

Reason: I found designs that I like, however: Spelling and grammar is critical. Please make sure that every word is spelled correctly. I am also changing my colors with my new business cards.

Target Market(s)

My clients have an average to above average income. They are health conscience and take good care of themselves. Into high end quality work and willing to pay for it.

Industry/Entity Type

It Professional

Font styles to use
Serif
Decorative
Script

Requirements
Must have
• Correct Spelling and grammar are a must. Please make sure everything is spelled correctly, punctuated properly and words are used exactly like I have it my brochure.
Nice to have
• Elegant and Classy
Should not have
• Nothing to do with Mobile Tanning.
On the front, I prefer the wording.... Call and Make your appointments at (843)555-0172. Visit us online at www.sunveiltan.com or email me at marla@sunveiltan.com

```html
<!DOCTYPE html>
<html lang="en">
<head>
<meta charset="utf-8">
<title>Sun Veil Custom Spray Tanning Studio – Inner Page</title>
<link href="https://fonts.googleapis.com/css2?family=Arimo:wght@700&family=Gelasio&family=Open+Sans:ital,wght@1,700&display=swap" rel="stylesheet">
<style>
  :root {
    --board: #1b1b1b;
    --maroon: #5a1515;
    --maroon-deep: #3f0b0b;
    --gold-light: #f3dc86;
    --gold: #dcbc5a;
    --gold-deep: #b8912f;
    --ink: #2a1a10;
    --white: #ffffff;
    --pool-light: #8fd3ef;
    --pool: #2a8fc4;
    --sky: #3d9bd8;
    --sand: #d9c9b0;
  }
  * { box-sizing: border-box; margin: 0; padding: 0; }
  html, body { width: 1200px; height: 900px; overflow: hidden; }
  body { background: var(--board); position: relative; font-family: "Gelasio", Georgia, serif; color: var(--ink); }

  .board-label {
    position: absolute; top: 22px; left: 0; width: 1200px; text-align: center;
    font-family: "Arimo", Arial, sans-serif; font-weight: 700; font-size: 36px;
    color: var(--white); letter-spacing: 0.5px;
  }

  .spread { position: absolute; left: 40px; top: 80px; width: 1125px; height: 777px; }
  .panel { position: absolute; top: 0; height: 777px; width: 375px; overflow: hidden; }
  .panel--left { left: 0; background: linear-gradient(180deg, var(--gold-light), var(--gold) 60%, var(--gold-deep)); }
  .panel--middle { left: 375px; background: radial-gradient(ellipse at 50% 40%, #6e1c1c, var(--maroon) 55%, var(--maroon-deep)); }
  .panel--right { left: 750px; background: linear-gradient(180deg, var(--gold-light), var(--gold) 55%, var(--gold-deep)); }

  .photo { position: absolute; }
  .photo--pool { left: 0; top: 0; width: 375px; height: 238px; background: linear-gradient(135deg, var(--pool-light), var(--pool)); }
  .photo--products { left: 68px; top: 18px; width: 280px; height: 234px; background: linear-gradient(180deg, #f4f4f4, #cfcfcf); border-radius: 4px; }
  .photo--beach { left: 0; top: 0; width: 375px; height: 390px; background: linear-gradient(180deg, var(--sky) 0%, #7fc0ea 60%, #3b83b5 72%, var(--sand) 100%); }

  .heading {
    display: inline-block; font-family: "Open Sans", Arial, sans-serif; font-style: italic; font-weight: 700;
    text-transform: uppercase; line-height: 1.05; white-space: nowrap;
  }
  .heading--dark { background: var(--maroon); color: var(--white); border: 1px solid #e9d9a8; box-shadow: 0 0 0 2px var(--maroon); }
  .heading--gold { background: linear-gradient(180deg, var(--gold-light), var(--gold)); color: var(--maroon); }

  .intro-heading { position: absolute; left: 19px; top: 242px; width: 334px; padding: 4px 6px; font-size: 17px; text-align: center; }
  .works-heading { position: absolute; left: 26px; top: 316px; padding: 7px 9px; font-size: 17px; }
  .services-heading { position: absolute; left: 28px; top: 399px; padding: 7px 9px; font-size: 17px; }

  .copy { position: absolute; font-size: 14px; line-height: 14.6px; }
  .copy .line { display: block; white-space: nowrap; }
  .copy p + p { margin-top: 14px; }
  .copy--left { left: 19px; top: 298px; width: 345px; }
  .copy--middle { left: 23px; width: 340px; color: var(--white); line-height: 14.5px; }
  .copy--lead { top: 263px; }
  .copy--works { top: 355px; }
  .copy--right { left: 26px; top: 578px; width: 340px; line-height: 15.7px; }

  .services { position: absolute; left: 26px; top: 439px; list-style: none; font-size: 14.5px; line-height: 18.2px; }
  .services li { position: relative; padding-left: 17px; white-space: nowrap; }
  .services li::before { content: ""; position: absolute; left: 0; top: 5px; width: 9px; height: 9px; border-radius: 50%; background: var(--maroon); }

  .swoosh { position: absolute; left: 0; top: 545px; width: 750px; height: 232px; }

  .address {
    position: absolute; left: 29px; top: 703px; width: 310px; height: 53px; border-radius: 27px;
    background: var(--maroon); border: 3px solid var(--gold-light); box-shadow: 0 0 0 2px var(--gold-deep);
    color: var(--white); font-family: "Open Sans", Arial, sans-serif; font-style: italic; font-weight: 700;
    font-size: 13px; line-height: 15px; text-align: center; padding-top: 9px; white-space: nowrap;
  }
</style>
</head>
<body>
  <div class="board-label">INNER PAGE</div>

  <main class="spread">
    <section class="panel panel--left">
      <div class="photo photo--pool" role="img" aria-label="Woman in striped bikini and straw hat floating in a swimming pool"></div>
      <h2 class="heading heading--dark intro-heading">Use Sun Veil to Glow for Healthy,<br>Radiant Skin</h2>
      <div class="copy copy--left">
        <p>
          <span class="line">Sun Veil proudly offers a leading spray tanning</span>
          <span class="line">product that will indulge your skin in a safe and</span>
          <span class="line">effective way. It achieves a natural result without sun</span>
          <span class="line">damage or premature aging in less than 10 minutes.</span>
          <span class="line">All sessions include our special mixture</span>
          <span class="line">of antioxidants and pure botanicals that leave your</span>
          <span class="line">skin radiant with a sun-kissed glow that can last</span>
          <span class="line">up to 7–10 days.</span>
        </p>
        <p>
          <span class="line">Our equipment is the most technologically</span>
          <span class="line">advanced system on the market. It is the only</span>
          <span class="line">system that delivers high-end beauty treatments</span>
          <span class="line">along with sunless tanning, all in one unique</span>
          <span class="line">system. In addition, it is the only sunless tanning</span>
          <span class="line">company to achieve “carbon neutral” status</span>
          <span class="line">and is proven to be the fastest, most consistent,</span>
          <span class="line">fully computerized system on the market.</span>
        </p>
      </div>
    </section>

    <section class="panel panel--middle">
      <div class="photo photo--products" role="img" aria-label="Spray tan product bottles and an exfoliating cream jar"></div>
      <div class="copy copy--middle copy--lead">
        <p>
          <span class="line">This ensures the highest quality true “spray and go”</span>
          <span class="line">which will allow our technicians to provide</span>
          <span class="line">top-of-the-line service.</span>
        </p>
      </div>
      <h2 class="heading heading--gold works-heading">How It Works?</h2>
      <div class="copy copy--middle copy--works">
        <p>
          <span class="line">Our sunless tan is just like the one you achieve</span>
          <span class="line">after hours of lying on the beach, and just like</span>
          <span class="line">a real tan, it will fade. Why? Every day, millions</span>
          <span class="line">of dead skin cells are worn away from the</span>
          <span class="line">surface of your skin. In fact, every 35 to 45 days,</span>
          <span class="line">you have an entirely new outer skin layer. This is</span>
          <span class="line">why the tan will gradually fade: as the dead cells</span>
          <span class="line">are worn away, so is the tan. Fading of this kind</span>
          <span class="line">applies to all tans, both sunless and real. To</span>
          <span class="line">maintain your tan, Sun Veil recommends tanning</span>
          <span class="line">2–3 times a month.</span>
        </p>
        <p>
          <span class="line">Following a skincare regimen is very important</span>
          <span class="line">for your spray tan. Twice a day, hydrate your skin</span>
          <span class="line">and drink plenty of water. Our skincare products</span>
          <span class="line">will help you enjoy a beautiful, long-lasting tan.</span>
        </p>
      </div>
    </section>

    <section class="panel panel--right">
      <div class="photo photo--beach" role="img" aria-label="Tanned woman in a black swimsuit standing on a sunny beach"></div>
      <h2 class="heading heading--dark services-heading">Services We Offer:</h2>
      <ul class="services">
        <li>Bronze tanning sessions</li>
        <li>Clear tanning sessions</li>
        <li>pH balance normalization treatments</li>
        <li>Anti-aging beauty elixirs</li>
        <li>Shimmer application</li>
        <li>Tanning packages for all types of<br>parties and events</li>
      </ul>
      <div class="copy copy--right">
        <p>
          <span class="line">Each session is applied by a certified tanning</span>
          <span class="line">technician who will not only give you the most</span>
          <span class="line">natural-looking customized spray tan, but will</span>
          <span class="line">leave your skin radiant and hydrated. In addition,</span>
          <span class="line">the tanning session will improve firmness</span>
          <span class="line">and camouflage spider veins while allowing you</span>
          <span class="line">to feel more confident on and off the beach.</span>
        </p>
      </div>
      <div class="address">418 W Harlow Lane, Myrtle Beach, SC 29577<br>Harbor Walk District</div>
    </section>

    <svg class="swoosh" viewBox="0 0 750 232" role="img" aria-label="Woman with a red flower in her hair relaxing in a black bikini by the pool">
      <defs>
        <linearGradient id="poolside" x1="0" y1="0" x2="1" y2="1">
          <stop offset="0" stop-color="#6fc6ea"/>
          <stop offset="0.6" stop-color="#2c95cc"/>
          <stop offset="1" stop-color="#1a5f8a"/>
        </linearGradient>
        <linearGradient id="goldEdge" x1="0" y1="0" x2="1" y2="0">
          <stop offset="0" stop-color="#b8912f"/>
          <stop offset="0.5" stop-color="#f3dc86"/>
          <stop offset="1" stop-color="#b8912f"/>
        </linearGradient>
      </defs>
      <path d="M0,36 C200,-2 470,24 722,232 L0,232 Z" fill="url(#poolside)"/>
      <path d="M0,36 C200,-2 470,24 722,232" fill="none" stroke="url(#goldEdge)" stroke-width="6"/>
    </svg>
  </main>
</body>
</html>
```